Maple Roster Business Card for recruitment company

We are looking for a Business Card Design that incorporates our personal details and our busines name and logo. We are a specialized search consultancy that recruit Property and Construction professionals.
We would like a business card that stands out and is appealing to the Construction and Property industry as well.

Target Market(s)

people in the construction and property industry

Contact Information for Business Card

Business Name and logo

Font styles to use
Serif

Colors
0094D4
00A9DD
6FCCEA
C7EBF8
E9F6FB

Requirements
Must have
• Business name and logo as well as contact details
Should not have
• No photos of us please

```html
<!DOCTYPE html>
<html lang="en">
<head>
<meta charset="UTF-8">
<title>Maple Roster — Business Card</title>
<link href="https://fonts.googleapis.com/css2?family=Montserrat:wght@300;600&family=Arimo:wght@400&display=swap" rel="stylesheet">
<style>
  :root {
    --backdrop: #1c1c1e;
    --card: #0a0a0b;
    --brand-blue: #0c5b7a;
    --link-blue: #0f6d92;
    --text-grey: #b9b9b9;
    --rule-grey: #4a4a4a;
  }
  * { margin: 0; padding: 0; box-sizing: border-box; }
  html, body {
    width: 1200px; height: 900px; overflow: hidden;
    background: var(--backdrop);
  }
  .sheet {
    width: 1200px; height: 900px;
    display: flex; align-items: center; justify-content: center; gap: 48px;
  }
  .card {
    position: relative;
    width: 540px; height: 309px;
    background: var(--card);
    box-shadow: 0 18px 40px rgba(0,0,0,.55);
  }
  .wordmark {
    font-family: "Montserrat", sans-serif;
    font-weight: 300;
    color: var(--brand-blue);
    letter-spacing: .04em;
    text-transform: uppercase;
    white-space: nowrap;
  }
  /* Back: details */
  .card-back {
    display: grid;
    grid-template-columns: 236px 1px 1fr;
    column-gap: 24px;
    padding: 56px 24px 56px 28px;
  }
  .brand-area {
    display: flex; align-items: center; justify-content: center;
    padding-top: 40px;
  }
  .card-back .wordmark { font-size: 23px; }
  .divider { background: var(--rule-grey); }
  .details {
    font-family: "Arimo", sans-serif;
    color: var(--text-grey);
    font-size: 13px; line-height: 1.35;
  }
  .person-name {
    font-family: "Montserrat", sans-serif;
    font-weight: 600; font-size: 15px;
    color: var(--brand-blue); letter-spacing: .02em;
    text-transform: uppercase;
  }
  .person-role { margin-bottom: 14px; }
  .contact-list { list-style: none; }
  .contact-list li { display: flex; align-items: center; gap: 8px; margin-bottom: 3px; white-space: nowrap; }
  .contact-list svg { width: 13px; height: 13px; fill: var(--brand-blue); flex: none; }
  .web-domain { color: var(--link-blue); }
  .address { margin-top: 14px; padding-left: 21px; white-space: nowrap; }
  /* Front: logo */
  .card-front .wordmark {
    position: absolute; left: 50%; top: 50%;
    transform: translate(-50%, -50%);
    font-size: 38px;
  }
</style>
</head>
<body>
<main class="sheet">
  <section class="card card-back" aria-label="Card back with contact details">
    <div class="brand-area"><div class="wordmark">Maple Roster</div></div>
    <div class="divider"></div>
    <div class="details">
      <p class="person-name">Daniel Hart</p>
      <p class="person-role">Managing Director</p>
      <ul class="contact-list">
        <li>
          <svg viewBox="0 0 24 24" aria-hidden="true"><path d="M6.6 10.8a15 15 0 0 0 6.6 6.6l2.2-2.2a1 1 0 0 1 1-.25 11.4 11.4 0 0 0 3.6.57 1 1 0 0 1 1 1V20a1 1 0 0 1-1 1A17 17 0 0 1 3 4a1 1 0 0 1 1-1h3.5a1 1 0 0 1 1 1c0 1.25.2 2.45.57 3.6a1 1 0 0 1-.25 1z"/></svg>
          044-555 018 240
        </li>
        <li>
          <svg viewBox="0 0 24 24" aria-hidden="true"><path d="M2 5h20v2l-10 7L2 7z"/><path d="M2 9l10 7 10-7v10H2z"/></svg>
          hello@mapleroster.com
        </li>
        <li>
          <svg viewBox="0 0 24 24" aria-hidden="true"><path d="M12 2a10 10 0 1 0 0 20 10 10 0 0 0 0-20zm6.9 6h-2.9a15 15 0 0 0-1.4-3.6A8 8 0 0 1 18.9 8zM12 4c.8 1.2 1.5 2.5 1.9 4h-3.8c.4-1.5 1.1-2.8 1.9-4zM4.3 14a8 8 0 0 1 0-4h3.4a16 16 0 0 0 0 4zm.8 2h2.9c.3 1.3.8 2.5 1.4 3.6A8 8 0 0 1 5.1 16zM8 8H5.1a8 8 0 0 1 4.3-3.6C8.8 5.5 8.3 6.7 8 8zm4 12c-.8-1.2-1.5-2.5-1.9-4h3.8c-.4 1.5-1.1 2.8-1.9 4zm2.3-6H9.7a14 14 0 0 1 0-4h4.6a14 14 0 0 1 0 4zm.3 5.6c.6-1.1 1.1-2.3 1.4-3.6h2.9a8 8 0 0 1-4.3 3.6zm1.7-5.6a16 16 0 0 0 0-4h3.4a8 8 0 0 1 0 4z"/></svg>
          <span>www.<span class="web-domain">mapleroster</span>.com</span>
        </li>
      </ul>
      <p class="address">18, Harbour Lane Suite 4<br>40210, Northbridge</p>
    </div>
  </section>

  <section class="card card-front" aria-label="Card front with business name">
    <div class="wordmark">Maple Roster</div>
  </section>
</main>
</body>
</html>
```